HearthMile business card and stationary design

We are looking for a simple yet elegant design for our mortgage company business card and stationary.

The card should include:
Name (Marcus Pell)
Title (CEO)
Phone Number (732-555-0182)
Address (48 Birchwell Court, Suite 314, Alder Bend, NJ 07948)
Email (email@hearthmile.example)
"NMLS" i.e. (NMLS 61947)
"Company NMLS" (Company NMLS 274615)

Contact Information for Business Card

See above

```html
<!DOCTYPE html>
<html lang="en">
<head>
<meta charset="utf-8">
<title>HearthMile Business Card</title>
<link rel="stylesheet" href="https://fonts.googleapis.com/css2?family=Montserrat:wght@400;500;600;700&display=swap">
<style>
  :root {
    --backdrop: #2b2d30;
    --navy: #1a2632;
    --sky: #27a3dd;
    --paper: #ffffff;
    --ink: #4a4f55;
    --muted: #6b7077;
  }
  * { box-sizing: border-box; margin: 0; padding: 0; }
  html, body {
    width: 1200px; height: 800px; overflow: hidden;
    background: var(--backdrop);
    font-family: "Montserrat", Arial, sans-serif;
  }
  .stage {
    position: relative; width: 1200px; height: 800px;
    display: flex; flex-direction: column; align-items: center; justify-content: center; gap: 40px;
  }
  .card {
    position: relative; width: 560px; height: 320px;
    box-shadow: 0 10px 28px rgba(0,0,0,.45);
    overflow: hidden;
  }
  .card-front {
    background: var(--navy);
    display: flex; flex-direction: column; align-items: center; justify-content: center;
  }
  .front-brand {
    color: var(--paper); font-weight: 600; font-size: 62px; letter-spacing: -1px; line-height: 1;
  }
  .license-line {
    margin-top: 16px; color: var(--paper); font-size: 11.5px; letter-spacing: 1px;
    display: flex; align-items: center; gap: 12px;
  }
  .license-divider { width: 1px; height: 12px; background: var(--sky); }
  .card-back { background: var(--paper); }
  .back-brand {
    position: absolute; left: 40px; top: 36px;
    color: var(--navy); font-weight: 600; font-size: 34px; letter-spacing: -.5px;
  }
  .address {
    position: absolute; left: 40px; top: 120px;
    color: var(--ink); font-size: 12.5px; line-height: 1.6;
  }
  .contact-list {
    position: absolute; left: 40px; top: 194px; list-style: none;
    color: var(--ink); font-size: 12.5px; line-height: 1.75;
  }
  .contact-item { display: flex; align-items: center; gap: 8px; }
  .contact-icon { width: 12px; height: 12px; fill: var(--sky); flex: none; }
  .person {
    position: absolute; right: 46px; top: 190px; text-align: right;
  }
  .person-name { color: var(--sky); font-weight: 600; font-size: 19px; letter-spacing: .5px; }
  .person-title { color: var(--muted); font-size: 12.5px; margin-top: 4px; letter-spacing: .5px; }
  .edge-tab {
    position: absolute; right: 0; top: 206px; width: 8px; height: 38px;
    background: var(--sky); border-radius: 4px 0 0 4px;
  }
</style>
</head>
<body>
<main class="stage">
  <section class="card card-front" aria-label="Business card front">
    <div class="front-brand">HearthMile</div>
    <div class="license-line">
      <span>NMLS 61947</span>
      <span class="license-divider"></span>
      <span>Company NMLS 274615</span>
    </div>
  </section>

  <section class="card card-back" aria-label="Business card back">
    <div class="back-brand">HearthMile</div>
    <p class="address">48 Birchwell Court, Suite 314<br>Alder Bend, NJ 07948</p>
    <ul class="contact-list">
      <li class="contact-item">
        <svg class="contact-icon" viewBox="0 0 24 24"><path d="M6.6 10.8a15.1 15.1 0 0 0 6.6 6.6l2.2-2.2c.3-.3.7-.4 1-.2 1.1.4 2.3.6 3.6.6.6 0 1 .4 1 1V20c0 .6-.4 1-1 1A17 17 0 0 1 3 4c0-.6.4-1 1-1h3.5c.6 0 1 .4 1 1 0 1.3.2 2.5.6 3.6.1.3 0 .7-.2 1z"/></svg>
        <span>732-555-0182</span>
      </li>
      <li class="contact-item">
        <svg class="contact-icon" viewBox="0 0 24 24"><path d="M2 5h20v2l-10 6L2 7z"/><path d="M2 9l10 6 10-6v10H2z"/></svg>
        <span>email@hearthmile.example</span>
      </li>
      <li class="contact-item">
        <svg class="contact-icon" viewBox="0 0 24 24"><circle cx="12" cy="12" r="10"/></svg>
        <span>www.hearthmile.example</span>
      </li>
    </ul>
    <div class="person">
      <div class="person-name">MARCUS PELL</div>
      <div class="person-title">CEO</div>
    </div>
    <div class="edge-tab"></div>
  </section>
</main>
</body>
</html>
```